2 x Digitize Logo | 2 x Business Cards | 2 x Fridge Magnets

We require 6 deliverables:
1. Residential logo redrawn (same just high quality for large print format).
2. Corporate logo redrawn (minor changes to wording and high quality for large print format).
3. New business card design for Furniture Removals (residential)
4. New business card design for Corporate Relocations (business)
5. New Fridge magnet for Furniture removals (residential)
6. New fridge magnet for Corporate Relocations (business)
1. Residential Logo
a. We require the logo to be translated into a high quality digital image with no modifications.
(see attached resilogo.jpg)
2. Residential Logo
a. We require the logo to be edited (add the word corporate relocations) be translated into a high quality digital image.
(see attached corplogo.jpg)
3. Using the resilogo please make a new business card for our business.
a. Please see the web site https://www.larkbendcarters.com.au for colours and inspiration.
b. The residential business card needs the following information:
i. Business Name (using the residential logo).
ii. Free Call: 1800 LB Cart (the L, B and Cart much be the same colour as the logo).
iii. Website: www.LarkbendCarters.com.au
iv. Address: 4/17 Ormsdale Court, VIC 3264
v. Email: cart@LarkbendCarters.com.au
vi. backof Card:
Review our service
www.PennantOrbit.com.au
Services: Local, Country, Interstate | Furniture Removals | Piano, Billiard Tables & Antiques
4. Using the corplogo please make a new business card for our business.
b. The corporate business card needs the following information:
i. Business Name (using the corporate logo).
v. Email: corporate@LarkbendCarters.com.au
vi. Back of Card:
Review our service
www.PennantOrbit.com.au
Services: Corporate relocations | Office equipment moves | Packing Service | Packing Materials
5. Using the resilogo please make a new fridge magent for our business.
b. The residential fidge magnet needs the following information:
iv. Services: Local, Country, Interstate | Furniture Removals | Piano, Billiard Tables & Antiques
6. Using the corplogo please make a new fridge magent for our business.
b. The corporate fidge magnet needs the following information:
iv. Services: Local, Country, Interstate | Corporate relocations
Target Market(s)
Residential Furniture Removals and Corporate Office relocations
Industry/Entity Type
Business
Contact Information for Business Card
Please see full brief for six items required
Requirements
Must have
- Clean simple, easy to read
Nice to have
- fresh, stand out, eye catching
Should not have
- plain, standard, boring, general

```html
<!DOCTYPE html>
<html lang="en">
<head>
<meta charset="utf-8">
<title>Larkbend Carters – Business Card</title>
<link href="https://fonts.googleapis.com/css2?family=Montserrat:wght@400;500;700;800&display=swap" rel="stylesheet">
<style>
  :root{
    --bg:#d9d9d9;
    --green:#2ab24c;
    --yellow:#fdc515;
    --red:#e1251b;
    --white:#ffffff;
    --ink:#555555;
  }
  *{margin:0;padding:0;box-sizing:border-box;}
  html,body{width:1200px;height:900px;overflow:hidden;background:var(--bg);font-family:"Montserrat",sans-serif;}
  .stage{position:relative;width:1200px;height:900px;}
  .card{position:absolute;left:250px;width:700px;height:400px;box-shadow:0 6px 18px rgba(0,0,0,.18);}
  .card--back{top:40px;background:var(--green);color:var(--white);text-align:center;padding:34px 56px 0;}
  .card--front{top:470px;background:var(--white);}

  .back__title{color:var(--yellow);font-weight:800;font-size:20px;margin-bottom:8px;}
  .back__services{font-weight:700;font-size:14px;line-height:1.45;margin-bottom:18px;}
  .review__name{display:inline-block;background:var(--yellow);color:var(--white);font-weight:700;font-size:14px;padding:3px 70px;border-radius:20px;margin-bottom:10px;}
  .review__text{font-size:11.5px;line-height:1.55;margin-bottom:18px;}

  .front__brand{position:absolute;left:44px;top:152px;display:flex;align-items:center;gap:8px;white-space:nowrap;}
  .brand__dot{width:10px;height:10px;border-radius:50%;background:var(--green);flex:none;}
  .brand__name{font-weight:800;font-size:20px;color:var(--green);letter-spacing:.2px;}
  .front__divider{position:absolute;left:342px;top:128px;width:2px;height:76px;background:var(--red);}
  .contact{position:absolute;left:366px;top:128px;list-style:none;}
  .contact__item{display:flex;align-items:center;gap:14px;font-size:15px;color:var(--ink);height:25px;white-space:nowrap;}
  .contact__item svg{width:16px;height:16px;flex:none;}
  .phone-word{font-weight:800;margin-left:6px;}
  .phone-word--l{color:var(--yellow);}
  .phone-word--b{color:var(--red);}
  .phone-word--cart{color:var(--green);}
  .front__address{position:absolute;left:0;right:0;top:330px;text-align:center;font-size:16px;color:var(--ink);}
  .front__address-label{color:var(--red);}
</style>
</head>
<body>
<main class="stage">
  <section class="card card--back">
    <h2 class="back__title">Service</h2>
    <p class="back__services">Local | Country | Interstate | Furniture<br>Removals | Piano | Billiard Tables &amp; Antiques</p>

    <span class="review__name">Milo</span>
    <p class="review__text">Well, what can I say? Booking process was easy, information clear and concise. Truck turned up exactly on time, Reid and Cole the right combination of friendly yet professional. Quick and efficient service, very careful with everything, no damage at all. Pricing was very acceptable.</p>

    <span class="review__name">Grant And Tess</span>
    <p class="review__text">Hugo and Cole delivered our new sideboard today, we would like to compliment the company for the efficient, friendly service these two gave us. On the basis of this experience we will not hesitate to use and recommend your company in the future. In short, your refrigerator magnet had gone straight to the pool room!! Thanks from two more satisfied customers.</p>
  </section>

  <section class="card card--front">
    <div class="front__brand">
      <span class="brand__dot"></span>
      <span class="brand__name">LARKBEND CARTERS</span>
    </div>
    <div class="front__divider"></div>
    <ul class="contact">
      <li class="contact__item">
        <svg viewBox="0 0 16 16"><path d="M4 1.5l2.5 3-1.5 1.5c.8 1.8 2.2 3.2 4 4l1.5-1.5 3 2.5-1.5 2.5C7 13 3 9 1.5 3z" fill="#2ab24c"/></svg>
        <span>Free Call: 1800 <span class="phone-word phone-word--l">L</span><span class="phone-word phone-word--b">B</span><span class="phone-word phone-word--cart">CART</span></span>
      </li>
      <li class="contact__item">
        <svg viewBox="0 0 16 16"><rect x="1" y="3" width="14" height="10" fill="#2ab24c"/><path d="M1 3l7 6 7-6" stroke="#fff" stroke-width="1.4" fill="none"/></svg>
        <span>cart@LarkbendCarters.com.au</span>
      </li>
      <li class="contact__item">
        <svg viewBox="0 0 16 16" fill="none" stroke="#2ab24c" stroke-width="1.4"><circle cx="8" cy="8" r="6.5"/><ellipse cx="8" cy="8" rx="3" ry="6.5"/><path d="M1.5 8h13M3 4.5h10M3 11.5h10"/></svg>
        <span>www.LarkbendCarters.com.au</span>
      </li>
    </ul>
    <p class="front__address"><span class="front__address-label">Address:</span> 4/17 Ormsdale Court, VIC 3264</p>
  </section>
</main>
</body>
</html>
```